Award-winnning Estate Agent needs a premium version of their 'For Sale' board design

We need a premium option for our 'For Sale' board design. We have a standard board that is attached to this brief, but were are looking to have a premium design version that we will use when selling exclusive properties. Our company name is Harbourline Vale Estates and the name for this is exclusive selection is: 'The Harbourline Collection'. The design needs to work with our current brand, but have a distinctive PREMIUM feel to it. I have uploaded the barnd guidelines and also some of the exisisting logo variations. We do NOT need a new logo but feel free to play around with colours, fonts, sizes etc. for the sign.

Target Market(s)

Property buyers & house hunters

Industry/Entity Type

Real Estate - Residential Property

Font styles to use
Sans Serif

Requirements
Must have
• A premium fee, must be square design, must be easy to read when driving past the sign
Nice to have
• I'm open ot ideas

```html
<!DOCTYPE html>
<html lang="en">
<head>
<meta charset="utf-8">
<title>Harbourline Vale Estates – For Sale Board</title>
<link rel="stylesheet" href="https://fonts.googleapis.com/css2?family=Montserrat:wght@500;600;700;800&display=swap">
<style>
  :root {
    --sky-blue: #1fa3de;
    --sky-blue-deep: #1a8dd4;
    --brand-purple: #422a6e;
    --footer-blue: #1079be;
    --tower-grey: #c8c8c8;
    --mark-blue: #4a73ad;
    --floor-grey: #ebebeb;
    --paper: #ffffff;
  }
  * { margin: 0; padding: 0; box-sizing: border-box; }
  html, body {
    width: 1200px;
    height: 2389px;
    overflow: hidden;
    background: var(--paper);
  }
  .canvas {
    position: relative;
    width: 1200px;
    height: 2389px;
    background: var(--paper);
    font-family: "Montserrat", Arial, sans-serif;
  }
  .scene-photo {
    position: absolute;
    left: 0; top: 0;
    width: 1200px; height: 916px;
    background: linear-gradient(180deg, #d9e8f3 0%, #c9d6dc 18%, #a87a55 38%, #8a6446 58%, #6f8a4a 78%, #7d9a3f 100%);
  }
  .scene-floor {
    position: absolute;
    left: 0; top: 916px;
    width: 1200px; height: 150px;
    background: var(--floor-grey);
  }
  .board {
    position: absolute;
    left: 111px;
    top: 1236px;
    width: 977px;
    height: 977px;
    background: var(--paper);
    box-shadow: 0 6px 14px rgba(0,0,0,0.25);
    overflow: hidden;
  }
  .sale-band {
    position: absolute;
    left: 0; top: 0;
    width: 100%; height: 231px;
    background: linear-gradient(180deg, var(--sky-blue) 0%, var(--sky-blue-deep) 60%, var(--sky-blue) 100%);
  }
  .sale-title {
    position: absolute;
    left: 0; top: 0;
    width: 100%; height: 231px;
    display: flex;
    align-items: center;
    justify-content: center;
    padding-top: 12px;
    color: var(--paper);
    font-weight: 700;
    font-size: 146px;
    letter-spacing: -2px;
    line-height: 1;
  }
  .rule {
    position: absolute;
    left: 0;
    width: 100%;
    background: var(--brand-purple);
  }
  .rule-top { top: 241px; height: 28px; }
  .rule-bottom { top: 594px; height: 30px; }
  .brand-panel {
    position: absolute;
    left: 0; top: 269px;
    width: 100%; height: 325px;
  }
  .side-tower {
    position: absolute;
    left: 0; top: 50px;
    width: 55px; height: 275px;
    background: var(--tower-grey);
  }
  .side-rooftops {
    position: absolute;
    right: 0; top: 270px;
    width: 173px; height: 55px;
    background: var(--brand-purple);
  }
  .brand-mark {
    position: absolute;
    left: 428px; top: 62px;
    width: 120px; height: 120px;
    background: var(--mark-blue);
  }
  .brand-name {
    position: absolute;
    left: 0; top: 226px;
    width: 100%;
    text-align: center;
    color: var(--brand-purple);
    font-weight: 600;
    font-size: 54px;
    letter-spacing: -0.5px;
    line-height: 1;
  }
  .contact-panel {
    position: absolute;
    left: 0; top: 631px;
    width: 100%; height: 346px;
    background: var(--footer-blue);
    color: var(--paper);
    text-align: center;
  }
  .collection-name {
    position: absolute;
    left: 0; top: 48px;
    width: 100%;
    font-weight: 800;
    font-size: 50px;
    text-transform: uppercase;
    line-height: 1;
  }
  .phone {
    position: absolute;
    left: 0; top: 124px;
    width: 100%;
    font-weight: 700;
    font-size: 112px;
    letter-spacing: -1px;
    line-height: 1;
  }
  .web {
    position: absolute;
    left: 0; top: 250px;
    width: 100%;
    font-weight: 600;
    font-size: 42px;
    letter-spacing: 4px;
    line-height: 1;
  }
</style>
</head>
<body>
<main class="canvas">
  <div class="scene-photo" role="img" aria-label="Photo of a modern timber house on a lawn with the For Sale board mounted between two concrete posts"></div>
  <div class="scene-floor"></div>
  <section class="board" aria-label="For Sale board">
    <div class="sale-band" role="img" aria-label="Blue band with a soft city skyline pattern"></div>
    <h1 class="sale-title">FOR SALE</h1>
    <div class="rule rule-top"></div>
    <div class="brand-panel">
      <div class="side-tower" role="img" aria-label="Grey clock tower decoration"></div>
      <div class="side-rooftops" role="img" aria-label="Purple rooftop decoration"></div>
      <div class="brand-mark"></div>
      <p class="brand-name">Harbourline Vale Estates</p>
    </div>
    <div class="rule rule-bottom"></div>
    <div class="contact-panel">
      <p class="collection-name">The Harbourline Collection</p>
      <p class="phone">01632960418</p>
      <p class="web">www.harbourlinevale.co.uk</p>
    </div>
  </section>
</main>
</body>
</html>
```